Mental Health care Company in Washington DC

We are a new mental health care services provider in Washington DC. Please look at these sites.
https://brightwaterfamilysupport.com
https://www.quietharborinc.com
https://willowgate-dc.org/
https://www.tidepathdc.com
https://www.thelanternofdc.com

```html
<!DOCTYPE html>
<html lang="en">
<head>
<meta charset="utf-8">
<title>Make An Appointment – Larkfield Health Services</title>
<link href="https://fonts.googleapis.com/css2?family=Outfit:wght@300;400;500;600&family=Roboto:wght@700&display=swap" rel="stylesheet">
<style>
:root{
  --aqua:#a3d9dd;
  --orange:#f4a662;
  --navy:#0c2340;
  --ink:#111418;
  --grey:#7c7f86;
  --line:#c9cdd3;
  --white:#ffffff;
  --dark:#051a3a;
  --req:#d8262c;
}
*{box-sizing:border-box;margin:0;padding:0}
html,body{width:680px;height:1200px;overflow:hidden}
body{font-family:"Outfit",sans-serif;background:var(--white);position:relative;color:var(--ink)}
.abs{position:absolute}

/* top bar */
.topbar{left:0;top:0;width:680px;height:70px;background:var(--aqua)}
.callbox{left:52px;top:13px;width:22px;height:22px;border:1px solid var(--white);border-radius:5px;display:flex;align-items:center;justify-content:center}
.call-small{left:77px;top:14px;font-size:6px;color:var(--white)}
.call-num{left:77px;top:19px;font-size:11px;color:var(--white)}
.nav{top:16px;font-size:8.5px;color:var(--white)}
.btn-top{left:519px;top:9px;width:119px;height:25px;background:var(--orange);border-radius:13px;color:var(--white);font-size:8.5px;display:flex;align-items:center;justify-content:center}

/* hero */
.hero{left:0;top:45px;width:680px;height:213px;border-radius:22px 22px 22px 0;background:linear-gradient(100deg,#eef7fb 0%,#f3f6f8 40%,#e6e9ec 62%,#d9c9bc 78%,#c99d86 92%,#b98a74 100%)}
.brand{font-weight:600;color:var(--navy);line-height:1;white-space:nowrap}
.hero-brand{left:47px;top:66px;font-size:21px}
.hero-brand small{display:block;font-size:7px;font-weight:600;letter-spacing:5px;margin-top:5px;padding-left:24px}
.hero-title{left:50px;top:156px;font-size:24px;font-weight:500;color:var(--ink)}

/* form */
.form-title{left:77px;top:300px;font-size:18px;font-weight:400;color:var(--orange)}
.form-rule{left:238px;top:312px;width:308px;height:1px;background:var(--orange)}
.label{font-size:7.2px;color:var(--grey)}
.label b{color:var(--req);font-weight:400}
.field{border:1px solid var(--line);border-radius:4px;background:var(--white);font-size:6.3px;color:var(--grey);padding-left:12px;display:flex;align-items:center;font-weight:300}
.field svg{position:absolute;right:9px;top:7px}
.check{top:482px;display:flex;align-items:center;gap:5px;font-size:6.5px;color:var(--grey);font-weight:300}
.check i{width:9px;height:9px;border:1px solid var(--line);border-radius:2px;display:block}
.textarea{align-items:flex-start;padding-top:10px}
.submit{left:78px;top:677px;width:496px;height:33px;background:var(--orange);border-radius:3px;color:var(--white);font-family:"Roboto",sans-serif;font-weight:700;font-size:10px;display:flex;align-items:center;justify-content:center}

/* footer */
.footer{left:0;top:769px;width:680px;height:388px;background:var(--aqua)}
.foot-brand{left:51px;top:799px;font-size:15px;color:var(--white)}
.foot-brand small{display:block;font-size:6px;letter-spacing:4px;margin-top:4px;padding-left:18px}
.tagline{left:194px;top:804px;font-size:11.5px;color:var(--white);font-weight:400;white-space:nowrap}
.social{top:804px;width:18px;height:18px;background:var(--orange);border-radius:3px}
.rule-w{height:1px;background:#8fbfc4}
.ft-h{font-size:11.5px;color:var(--white);font-weight:500;line-height:1.4}
.ft-t{font-size:7px;color:var(--ink);font-weight:400}
.ft-b{font-size:7px;color:var(--ink);font-weight:600;line-height:1.45}
.nl-line{left:58px;width:167px;height:1px;background:#87b8bd}
.nl-btn{left:58px;top:985px;width:39px;height:17px;border-radius:9px;background:var(--orange);color:var(--white);font-size:7px;display:flex;align-items:center;justify-content:center}
.ql{left:288px;font-size:7.2px;color:var(--ink);display:flex;align-items:center;gap:5px}
.ico{display:flex;align-items:center;gap:4px}
.phone-pill{left:444px;top:1010px;width:176px;height:37px;border-radius:19px;background:var(--orange);color:var(--white);font-size:15.5px;font-weight:500;display:flex;align-items:center;justify-content:center;gap:8px}
.sched-h{left:59px;top:1018px;font-size:15.5px;color:var(--white);font-weight:500}
.sched-p{left:59px;top:1045px;width:340px;font-size:7px;line-height:1.45;color:var(--ink)}
.disclaimer{left:58px;top:1102px;width:566px;font-size:5.8px;line-height:1.5;text-align:center;color:var(--ink)}
.bottombar{left:0;top:1157px;width:680px;height:43px;background:var(--dark)}
.copy{top:1171px;font-size:7.2px;color:var(--white)}
</style>
</head>
<body>

<header>
  <div class="abs topbar"></div>
  <div class="abs callbox">
    <svg width="12" height="12" viewBox="0 0 24 24" fill="none" stroke="#fff" stroke-width="1.6"><path d="M5 3h4l2 5-2.5 1.5a11 11 0 0 0 6 6L16 13l5 2v4a2 2 0 0 1-2 2A16 16 0 0 1 3 5a2 2 0 0 1 2-2z"/></svg>
  </div>
  <div class="abs call-small">Call us today:</div>
  <div class="abs call-num">202-555-0147</div>
  <nav>
    <span class="abs nav" style="left:246px">Home</span>
    <span class="abs nav" style="left:294px">About</span>
    <span class="abs nav" style="left:344px">Services</span>
    <span class="abs nav" style="left:402px">Contact</span>
  </nav>
  <div class="abs btn-top">Make an Appointment</div>
</header>

<section>
  <div class="abs hero" role="img" aria-label="Photo of a hand writing with a pen on a planner"></div>
  <div class="abs brand hero-brand">Larkfield Health<small>SERVICES</small></div>
  <h1 class="abs hero-title">Make An Appointment</h1>
</section>

<main>
  <h2 class="abs form-title">Appointment Form</h2>
  <div class="abs form-rule"></div>

  <div class="abs label" style="left:77px;top:349px">Enter your First name<b>*</b></div>
  <div class="abs field" style="left:77px;top:363px;width:244px;height:28px"></div>
  <div class="abs label" style="left:331px;top:351px">Enter your Last name<b>*</b></div>
  <div class="abs field" style="left:331px;top:363px;width:244px;height:28px"></div>

  <div class="abs label" style="left:77px;top:407px">Date of Birth (DOB)<b>*</b></div>
  <div class="abs field" style="left:77px;top:422px;width:151px;height:28px">mm/dd//yyyy
    <svg width="12" height="13" viewBox="0 0 12 13" fill="none" stroke="#7c7f86" stroke-width=".8"><rect x="1" y="2" width="10" height="10" rx="2"/><path d="M1 5h10M4 1v2M8 1v2"/><circle cx="4" cy="7.5" r=".4"/><circle cx="6" cy="7.5" r=".4"/><circle cx="8" cy="7.5" r=".4"/><circle cx="4" cy="9.5" r=".4"/><circle cx="6" cy="9.5" r=".4"/><circle cx="8" cy="9.5" r=".4"/></svg>
  </div>
  <div class="abs label" style="left:246px;top:407px">Phone<b>*</b></div>
  <div class="abs field" style="left:246px;top:422px;width:151px;height:28px">Enter your Last name</div>
  <div class="abs label" style="left:414px;top:407px">Email<b>*</b></div>
  <div class="abs field" style="left:414px;top:422px;width:151px;height:28px">Enter your Last name</div>

  <div class="abs label" style="left:77px;top:466px">Which services are you interested in?<b>*</b></div>
  <label class="abs check" style="left:77px"><i></i>Personal consultation</label>
  <label class="abs check" style="left:162px"><i></i>Group therapy</label>
  <label class="abs check" style="left:223px"><i></i>Online therapy</label>
  <label class="abs check" style="left:284px"><i></i>Couple problem</label>

  <div class="abs label" style="left:77px;top:508px">Appointment Date <b>*</b></div>
  <div class="abs field" style="left:77px;top:523px;width:151px;height:28px">Enter preferred date here
    <svg width="12" height="13" viewBox="0 0 12 13" fill="none" stroke="#7c7f86" stroke-width=".8"><rect x="1" y="2" width="10" height="10" rx="2"/><path d="M1 5h10M4 1v2M8 1v2"/><circle cx="4" cy="7.5" r=".4"/><circle cx="6" cy="7.5" r=".4"/><circle cx="8" cy="7.5" r=".4"/><circle cx="4" cy="9.5" r=".4"/><circle cx="6" cy="9.5" r=".4"/><circle cx="8" cy="9.5" r=".4"/></svg>
  </div>
  <div class="abs label" style="left:246px;top:508px">Appointment Time <b>*</b></div>
  <div class="abs field" style="left:246px;top:523px;width:151px;height:28px">Select preferred time
    <svg width="10" height="10" viewBox="0 0 10 10" fill="none" stroke="#333" stroke-width="1" style="top:9px"><path d="M2 3.5l3 3 3-3"/></svg>
  </div>

  <div class="abs label" style="left:77px;top:567px">Your Comments/Questions <b>*</b></div>
  <div class="abs field textarea" style="left:78px;top:584px;width:497px;height:77px">Enter your message</div>

  <div class="abs submit">SUBMIT NOW</div>
</main>

<footer>
  <div class="abs footer"></div>
  <div class="abs brand foot-brand">Larkfield Health<small>SERVICES</small></div>
  <div class="abs tagline">Find out how we approach our client’s treatment and therapy !</div>
  <div class="abs social" style="left:536px"></div>
  <div class="abs social" style="left:559px"></div>
  <div class="abs social" style="left:582px"></div>
  <div class="abs social" style="left:605px"></div>
  <div class="abs rule-w" style="left:53px;top:845px;width:570px"></div>

  <div class="abs ft-h" style="left:58px;top:876px">Sign Up for Our<br>Newsletter</div>
  <div class="abs ft-t" style="left:59px;top:921px">Enter Your Name</div>
  <div class="abs nl-line" style="top:937px"></div>
  <div class="abs ft-t" style="left:59px;top:955px">Enter Your Email</div>
  <div class="abs nl-line" style="top:972px"></div>
  <div class="abs nl-btn">Submit</div>

  <div class="abs ft-h" style="left:288px;top:872px">Quick Links</div>
  <div class="abs ql" style="top:898px"><svg width="5" height="7" viewBox="0 0 5 7" fill="none" stroke="#111" stroke-width="1"><path d="M1 1l2.5 2.5L1 6"/></svg>Home</div>
  <div class="abs ql" style="top:915px"><svg width="5" height="7" viewBox="0 0 5 7" fill="none" stroke="#111" stroke-width="1"><path d="M1 1l2.5 2.5L1 6"/></svg>About</div>
  <div class="abs ql" style="top:932px"><svg width="5" height="7" viewBox="0 0 5 7" fill="none" stroke="#111" stroke-width="1"><path d="M1 1l2.5 2.5L1 6"/></svg>Services</div>
  <div class="abs ql" style="top:948px"><svg width="5" height="7" viewBox="0 0 5 7" fill="none" stroke="#111" stroke-width="1"><path d="M1 1l2.5 2.5L1 6"/></svg>Contact</div>

  <div class="abs ft-h" style="left:414px;top:873px">Get In Touch</div>
  <div class="abs ft-t ico" style="left:414px;top:902px"><svg width="9" height="9" viewBox="0 0 24 24" fill="none" stroke="#111" stroke-width="1.8"><path d="M5 3h4l2 5-2.5 1.5a11 11 0 0 0 6 6L16 13l5 2v4a2 2 0 0 1-2 2A16 16 0 0 1 3 5a2 2 0 0 1 2-2z"/></svg>Call Us</div>
  <div class="abs ft-b" style="left:414px;top:914px">202-555-0147</div>
  <div class="abs ft-t ico" style="left:521px;top:903px"><svg width="9" height="9" viewBox="0 0 10 10" fill="none" stroke="#111" stroke-width=".9"><circle cx="5" cy="5" r="4"/><path d="M5 2.8V5l1.5 1"/></svg>e-mail us</div>
  <div class="abs ft-b" style="left:521px;top:915px">info@larkfieldhealth.com</div>
  <div class="abs ft-t ico" style="left:414px;top:939px"><svg width="9" height="9" viewBox="0 0 10 10" fill="none" stroke="#111" stroke-width=".9"><circle cx="5" cy="5" r="4"/><path d="M5 2.8V5l1.5 1"/></svg>Location Hours</div>
  <div class="abs ft-b" style="left:414px;top:951px">Mon – Fri: 9:00 – 6:00<br>Sat: 10 – 4:00</div>
  <div class="abs ft-t ico" style="left:519px;top:940px"><svg width="9" height="10" viewBox="0 0 10 12" fill="none" stroke="#111" stroke-width=".9"><path d="M5 11s4-4 4-6.5A4 4 0 0 0 1 4.5C1 7 5 11 5 11z"/><circle cx="5" cy="4.5" r="1.4"/></svg>Address</div>
  <div class="abs ft-b" style="left:519px;top:952px">1840 Juniper Row, Suite 210,<br>Washington, DC 20012</div>

  <div class="abs sched-h">Schedule Your Appointment</div>
  <p class="abs sched-p">It is a long established fact that a reader will be distracted by the readable content of a page when looking at its layout. The point of using Lorem Ipsum is that it has a more-or-less normal.</p>
  <div class="abs phone-pill">
    <svg width="16" height="16" viewBox="0 0 24 24" fill="none" stroke="#fff" stroke-width="2"><path d="M5 3h4l2 5-2.5 1.5a11 11 0 0 0 6 6L16 13l5 2v4a2 2 0 0 1-2 2A16 16 0 0 1 3 5a2 2 0 0 1 2-2z"/><path d="M14 3a7 7 0 0 1 7 7M14 6.5a3.5 3.5 0 0 1 3.5 3.5"/></svg>
    1-202-555-0147
  </div>

  <div class="abs rule-w" style="left:59px;top:1078px;width:561px"></div>
  <p class="abs disclaimer">This website is for mental health care services purposes only.It is a long established fact that a reader will be distracted by the readable content of a page when looking at its layout. The point of using Lorem Ipsum is that it has a more-or-less normal distribution of letters, as opposed to using ‘Content here, content here’, making it look like readable English. Many desktop publishing packages and web page editors now use Lorem Ipsum as their default model text, and a search for ‘lorem ipsum’ will uncover many web sites still in their infancy.</p>

  <div class="abs bottombar"></div>
  <div class="abs copy" style="left:48px">Copyright © 2025 larkfieldhealth.com</div>
  <div class="abs copy" style="left:497px">Privacy Policy | Client Terms of Service</div>
</footer>

</body>
</html>
```